Business Cards for new orthopaedic surgery practice

My husband and I are starting our own orthopaedic surgery practice. We are looking for a business card that is uniform, but one will have my name/title and the other will have his. You can just create one design with my name on it for now. But when I choose your design as the winning design I will ask that you add another copy with his name/title.

We are looking for classy, simple, elite all in one. We like dark blues/a little gold/yellow. Something that goes with our logo. We want our logo incorporated. Here is all the info you need:
Business name: RV Bone & Vitality Center
Location: 38517 North Willowmere Ave
Maple Harbor, FL 33958
Phone: 954-218-4063
Fax: 954-582-7341
Email: info@myrvbonecare.example

Names: Lydia Vance, M.D.
Board Certified Hand and Upper Extremity Surgeon

Ebo Dansu, M.D.
Board Certified Hip & Knee Replacement/General Orthopaedic Surgeon

Can decide what you want to put on the back. Maybe a slogan:
Grounded in Skill. Devoted to You

I am just going to upload our logo. The only thing is if we select you as the winning design, the location, and phone numbers may change. We will need your help to update that once fully solidified.

Industry/Entity Type

Medical

Contact Information for Business Card

Colors
0054AA
0677BA
7BADD7
CADEEF
E8F1F8
0094D4
00A9DD
6FCCEA
C7EBF8
E9F6FB

Requirements
Must have
• class, appeal,
Should not have
• We want to air on the side of masculine if we are looking at masculine vs. feminine feel. But we still want it classy, sophisticated, and something we will love

```html
<!DOCTYPE html>
<html lang="en">
<head>
<meta charset="utf-8">
<title>RV Bone &amp; Vitality Center — Business Card</title>
<link href="https://fonts.googleapis.com/css2?family=Cinzel:wght@600;700&family=Montserrat:wght@400;500;600&display=swap" rel="stylesheet">
<style>
  :root {
    --backdrop: #2b2b2d;
    --navy: #1c2a52;
    --emboss: #34487e;
    --gold: #c9a45a;
    --white: #ffffff;
    --muted: #e7ecf6;
  }
  * { box-sizing: border-box; margin: 0; padding: 0; }
  html, body {
    width: 1200px; height: 875px; overflow: hidden;
    background: var(--backdrop);
  }
  .canvas { position: relative; width: 1200px; height: 875px; }

  .card {
    position: absolute;
    width: 560px; height: 320px;
    background: var(--navy);
    border-radius: 18px;
    box-shadow: 0 10px 30px rgba(0,0,0,.45);
    overflow: hidden;
  }
  .card--back { left: 30px; top: 120px; }
  .card--front { left: 610px; top: 435px; }

  .brand {
    position: absolute;
    display: flex; align-items: center; justify-content: center;
    border-radius: 50%;
    text-align: center;
    font-family: "Cinzel", serif;
    font-weight: 600;
    letter-spacing: .12em;
    line-height: 1.35;
  }
  .card--back .brand {
    left: 195px; top: 38px; width: 170px; height: 170px;
    border: 2px solid var(--emboss);
    color: var(--emboss);
    font-size: 15px;
  }
  .card--front .brand {
    left: 340px; top: 48px; width: 190px; height: 190px;
    border: 2px solid var(--gold);
    color: var(--white);
    font-size: 17px;
  }

  .slogan {
    position: absolute; left: 0; right: 0; bottom: 44px;
    text-align: center;
    font-family: "Montserrat", sans-serif;
    font-weight: 600; font-size: 17px;
    color: var(--gold);
    letter-spacing: .01em;
  }

  .accent-bar {
    position: absolute; left: 0; top: 70px;
    width: 14px; height: 62px;
    background: var(--gold);
  }
  .identity { position: absolute; left: 34px; top: 72px; }
  .identity__name {
    font-family: "Cinzel", serif; font-weight: 700;
    font-size: 21px; color: var(--gold); letter-spacing: .02em;
  }
  .identity__title {
    margin-top: 4px;
    font-family: "Montserrat", sans-serif; font-weight: 400;
    font-size: 12.5px; line-height: 1.3; color: var(--white);
  }

  .contact {
    position: absolute; left: 34px; top: 190px;
    font-family: "Montserrat", sans-serif; font-size: 12.5px;
    color: var(--muted); line-height: 1.35;
  }
  .contact__address { margin-bottom: 12px; }
  .contact__row { display: flex; align-items: center; gap: 7px; }
  .contact__icon { width: 11px; height: 11px; flex: none; }
</style>
</head>
<body>
<main class="canvas">

  <section class="card card--back" aria-label="Card back">
    <div class="brand">RV Bone &amp;<br>Vitality<br>Center</div>
    <p class="slogan">Grounded in Skill. Devoted to You</p>
  </section>

  <section class="card card--front" aria-label="Card front">
    <span class="accent-bar"></span>
    <div class="identity">
      <h1 class="identity__name">LYDIA VANCE, M.D.</h1>
      <p class="identity__title">Board Certified Hand and Upper<br>Extremity Surgeon</p>
    </div>

    <div class="contact">
      <p class="contact__address">38517 North Willowmere Ave<br>Maple Harbor, FL 33958</p>
      <p class="contact__row">
        <svg class="contact__icon" viewBox="0 0 12 12" aria-hidden="true"><path fill="#c9a45a" d="M2.5 1 4.3 1 5 3.6 3.9 4.6C4.5 6 5.9 7.4 7.4 8.1L8.4 7 11 7.7 11 9.5C11 10.3 10.3 11 9.5 11 5 11 1 7 1 2.5 1 1.7 1.7 1 2.5 1Z"/></svg>
        954-218-4063
      </p>
      <p class="contact__row">
        <svg class="contact__icon" viewBox="0 0 12 12" aria-hidden="true"><g fill="#c9a45a"><rect x="3" y="1" width="6" height="3"/><rect x="1" y="4.5" width="10" height="4.5" rx="1"/><rect x="3" y="8" width="6" height="3"/></g></svg>
        954-582-7341
      </p>
      <p class="contact__row">
        <svg class="contact__icon" viewBox="0 0 12 12" aria-hidden="true"><rect x="1" y="2.5" width="10" height="7" fill="#c9a45a"/><path d="M1 2.5 6 6.5 11 2.5" fill="none" stroke="#1c2a52" stroke-width="1"/></svg>
        info@myrvbonecare.example
      </p>
    </div>

    <div class="brand">RV Bone &amp;<br>Vitality<br>Center</div>
  </section>

</main>
</body>
</html>
```